KRT Engineering Business Card Design

We’re looking for an elegant, clean, and timeless business card design that communicates experience, capability, and reliability.

KRT Engineering was established in 1995 , we are a Government Contracting company providing Professional Services to the Office of Frontier Affairs, Harbor Protection and the Vantage Collective. Our capabilities include: Acquisition & Program Management; Intelligence & Security Operations; Cyber, IT & Network Operations; Lifecycle Logistics & Asset Readiness; C5ISR Systems Engineering & Sustainment.

We want the card to reflect a straightforward, confident approach to business. The design should feel polished and professional without being flashy or overly corporate.

Design Direction
Clean, sophisticated, and uncluttered
Elegant but understated
Strong typography and thoughtful spacing
A timeless aesthetic rather than something overly trendy
Confident and established, with a sense of substance
Easy to read and practical in a real-world business setting

The overall impression should be: “These are experienced professionals who know what they’re doing, do what they say, and can be relied upon.”

We’re open to creative interpretations. The finished card should feel distinctive through its typography, proportions, layout, and attention to detail rather than through excessive graphics or visual effects.

We’re looking for a design that would make a potential client immediately feel that they’re dealing with a capable, trustworthy, and established company.

Company Colors: Navy and Gold/Yellow (but you do not need to use these colors on the card)
Company Name: KRT Engineering Associates, Inc. (known as KRT Engineering)
Website: krtengineering.com
Company Logo: Navy & Gold (other variations attached)

```html
<!DOCTYPE html>
<html lang="en">
<head>
<meta charset="utf-8">
<title>KRT Engineering Business Card</title>
<link rel="stylesheet" href="https://fonts.googleapis.com/css2?family=Inter:wght@700;800&family=Poppins:wght@400&display=swap">
<style>
  :root {
    --navy: #252c5e;
    --navy-deep: #1d2350;
    --gold: #fde34e;
    --ink: #222a5a;
    --paper: #ffffff;
    --backdrop: #8a8b8f;
  }
  * { box-sizing: border-box; margin: 0; padding: 0; }
  html, body {
    width: 900px; height: 1200px; overflow: hidden;
    background: var(--backdrop);
  }
  .canvas { position: relative; width: 900px; height: 1200px; }

  .card { position: absolute; left: 136px; width: 630px; height: 363px; overflow: hidden; }

  .card-front {
    top: 214px;
    background: linear-gradient(135deg, #242b5a 0%, #2c3468 100%);
  }
  .card-front .wordmark {
    position: absolute; left: 0; right: 0; top: 150px;
    display: flex; align-items: center; justify-content: center; gap: 14px;
    font-family: "Inter", sans-serif; font-weight: 800; font-size: 96px;
    line-height: 1; letter-spacing: -2px; color: var(--navy-deep);
  }
  .card-front .wordmark-dot {
    width: 22px; height: 22px; border-radius: 50%; background: var(--gold);
  }

  .card-back { top: 629px; background: var(--paper); color: var(--ink); }
  .holder {
    position: absolute; left: 42px; top: 50px;
    font-family: "Inter", sans-serif; font-weight: 700; font-size: 24px;
    letter-spacing: -0.3px;
  }
  .role {
    position: absolute; left: 43px; top: 82px;
    font-family: "Poppins", sans-serif; font-size: 16.5px;
  }
  .rule { position: absolute; left: 43px; width: 149px; height: 1.5px; background: var(--ink); }
  .rule-top { top: 115px; }
  .rule-bottom { top: 208px; }
  .address {
    position: absolute; left: 43px; top: 124px;
    font-family: "Poppins", sans-serif; font-size: 16.5px; line-height: 25px;
    font-style: normal;
  }
  .contacts {
    position: absolute; left: 43px; top: 222px; list-style: none;
    font-family: "Poppins", sans-serif; font-size: 17px; letter-spacing: 0.3px;
  }
  .contacts li { display: flex; align-items: center; gap: 6px; height: 28px; margin-bottom: 2px; }
  .contacts li:nth-child(3) { margin-top: 3px; }
  .contact-icon { width: 18px; height: 18px; flex: none; }

  .card-back .wordmark {
    position: absolute; left: 355px; top: 158px;
    display: flex; align-items: center; gap: 10px;
    font-family: "Inter", sans-serif; font-weight: 800; font-size: 80px;
    line-height: 1; letter-spacing: -2px; color: var(--navy);
  }
  .card-back .wordmark-dot {
    width: 18px; height: 18px; border-radius: 50%; background: var(--gold);
  }

  .footer-band { position: absolute; left: 0; bottom: 0; width: 630px; height: 20px; }
</style>
</head>
<body>
<main class="canvas">
  <section class="card card-front" aria-label="Card front">
    <div class="wordmark"><span>KRT</span><span class="wordmark-dot"></span></div>
  </section>

  <section class="card card-back" aria-label="Card back">
    <h1 class="holder">Marian Keller, P.E.</h1>
    <p class="role">CEO &amp; President</p>
    <div class="rule rule-top"></div>
    <address class="address">4820 Harbor Ridge Road,<br>Suite 310, Norfolk Bay,<br>VA 23519</address>
    <div class="rule rule-bottom"></div>
    <ul class="contacts">
      <li>
        <svg class="contact-icon" viewBox="0 0 18 18" aria-hidden="true">
          <circle cx="9" cy="9" r="9" fill="#222a5a"/>
          <path d="M6 4.5c.5-.3 1-.2 1.3.3l.9 1.6c.2.4.1.9-.2 1.2l-.6.5c.5 1.1 1.3 1.9 2.4 2.4l.5-.6c.3-.3.8-.4 1.2-.2l1.6.9c.5.3.6.8.3 1.3l-.6.9c-.4.5-1 .7-1.6.5C8.6 12.6 5.4 9.4 4.7 6.7c-.2-.6 0-1.2.5-1.6z" fill="#fde34e"/>
        </svg>
        <span>757-555-0148</span>
      </li>
      <li>
        <svg class="contact-icon" viewBox="0 0 18 18" aria-hidden="true">
          <circle cx="9" cy="9" r="9" fill="#fde34e"/>
          <circle cx="9" cy="9" r="6" fill="none" stroke="#222a5a" stroke-width="1.3"/>
          <ellipse cx="9" cy="9" rx="2.6" ry="6" fill="none" stroke="#222a5a" stroke-width="1.1"/>
          <path d="M3 9h12M4 6h10M4 12h10" stroke="#222a5a" stroke-width="1"/>
        </svg>
        <span>krtengineering.com</span>
      </li>
      <li>
        <svg class="contact-icon" viewBox="0 0 18 18" aria-hidden="true">
          <circle cx="9" cy="9" r="9" fill="#fde34e"/>
          <circle cx="9" cy="9" r="5" fill="#222a5a"/>
        </svg>
        <span>krt-engineering-associates-inc</span>
      </li>
    </ul>
    <div class="wordmark"><span>KRT</span><span class="wordmark-dot"></span></div>
    <svg class="footer-band" viewBox="0 0 630 20" aria-hidden="true">
      <polygon points="0,0 529,0 518,20 0,20" fill="#252c5e"/>
      <polygon points="538,0 630,0 630,20 527,20" fill="#fde34e"/>
    </svg>
  </section>
</main>
</body>
</html>
```